Corporate Business Card

Very professional, Modern, Not to busy, include phone address email, website
(253) 617-4930, 18761 52nd Avenue S, Kent, WA 98047, martin@plumlinegroup.com, varkoworks.com

Target Market(s)

Manufacturing

Industry/Entity Type

Aero, machining, manufacturing, Off road racing

Contact Information for Business Card

Phone, address email, website

```html
<!DOCTYPE html>
<html lang="en">
<head>
<meta charset="utf-8">
<title>Varko Industries — Business Card</title>
<link rel="stylesheet" href="https://fonts.googleapis.com/css2?family=Open+Sans:wght@400;600;700&display=swap">
<style>
  :root {
    --backdrop: #dcd8d1;
    --card-light: #eef0f2;
    --navy: #1e3862;
    --navy-deep: #182f55;
    --red: #b3262b;
    --cream: #e8e1d2;
    --text-light: #d6d9de;
  }
  * { margin: 0; padding: 0; box-sizing: border-box; }
  html, body {
    width: 1200px; height: 1200px; overflow: hidden;
    background: var(--backdrop);
    font-family: "Open Sans", Arial, sans-serif;
  }
  .card {
    position: absolute; left: 100px; top: 327px;
    width: 1000px; height: 546px;
    border-radius: 30px; overflow: hidden;
    background: var(--card-light);
    box-shadow: 0 10px 30px rgba(0,0,0,0.15);
  }
  .card-shapes { position: absolute; inset: 0; }
  .brand {
    position: absolute; left: 0; right: 0; top: 70px;
    text-align: center;
    font-weight: 700; font-size: 64px; letter-spacing: 1px;
    color: var(--navy);
  }
  .contact {
    position: absolute; top: 368px;
    font-size: 25px; line-height: 36px; color: var(--text-light);
  }
  .contact-address { right: 600px; text-align: right; }
  .contact-address .company { color: var(--red); font-weight: 600; }
  .divider {
    position: absolute; left: 438px; top: 378px;
    width: 2px; height: 102px; background: var(--red);
  }
  .contact-lines { left: 470px; }
  .contact-lines li { list-style: none; display: flex; align-items: center; gap: 10px; }
  .icon { width: 20px; height: 20px; fill: var(--red); flex: none; }
</style>
</head>
<body>
  <div class="card">
    <svg class="card-shapes" viewBox="0 0 1000 546" width="1000" height="546">
      <path d="M0 160 Q500 440 1000 160 L1000 546 L0 546 Z" fill="var(--navy)"/>
      <path d="M0 148 Q500 418 1000 148" fill="none" stroke="var(--cream)" stroke-width="14"/>
      <path d="M0 144 Q500 408 1000 144" fill="none" stroke="var(--red)" stroke-width="7"/>
    </svg>

    <div class="brand">Varko Industries</div>

    <div class="contact contact-address">
      <div class="company">Varko Industries</div>
      <div>18761 52nd Avenue S</div>
      <div>Kent, WA 98047</div>
    </div>

    <div class="divider"></div>

    <ul class="contact contact-lines">
      <li>
        <svg class="icon" viewBox="0 0 24 24"><path d="M6.6 10.8a15 15 0 0 0 6.6 6.6l2.2-2.2a1 1 0 0 1 1-.25 11.4 11.4 0 0 0 3.6.57 1 1 0 0 1 1 1V20a1 1 0 0 1-1 1A17 17 0 0 1 3 4a1 1 0 0 1 1-1h3.5a1 1 0 0 1 1 1c0 1.25.2 2.45.57 3.6a1 1 0 0 1-.25 1z"/></svg>
        (253) 617-4930
      </li>
      <li>
        <svg class="icon" viewBox="0 0 24 24"><path d="M2 5h20v14H2z M2 5l10 8 10-8" stroke="#1e3862" stroke-width="1.5"/></svg>
        martin@plumlinegroup.com
      </li>
      <li>
        <svg class="icon" viewBox="0 0 24 24"><circle cx="12" cy="12" r="10"/><path d="M2 12h20M12 2c3 3 3 17 0 20M12 2c-3 3-3 17 0 20" fill="none" stroke="#1e3862" stroke-width="1.3"/></svg>
        varkoworks.com
      </li>
    </ul>
  </div>
</body>
</html>
```